Stonebridge Building and Projects business cards

A business card with watermark background (construction work)

Company logo attached

Home improvement projects
House renovations
Bathroom and kitchen renovations
House extensions
New builds and granny flats

Director Omar Haddani
(Phone number)
omar@sbpbuilding.com.au
(Instagram logo) sbp_building

```html
<!DOCTYPE html>
<html lang="en">
<head>
<meta charset="utf-8">
<title>Stonebridge Building and Projects – Business Cards</title>
<link rel="stylesheet" href="https://fonts.googleapis.com/css2?family=Lato:wght@400;700&family=Oswald:wght@500&family=Arimo:wght@400&display=swap">
<style>
  :root {
    --stage: #2b2b2c;
    --card: #1b1b1c;
    --brand-blue: #2f76c0;
    --text-light: #e9e9ea;
    --text-muted: #cfcfd1;
    --divider: #8a8a8c;
  }
  * { box-sizing: border-box; margin: 0; padding: 0; }
  html, body {
    width: 1200px; height: 900px; overflow: hidden;
    background: var(--stage);
  }
  .stage {
    position: relative; width: 1200px; height: 900px;
  }
  .card {
    position: absolute; left: 290px;
    width: 620px; height: 354px;
    background: var(--card);
    box-shadow: 0 10px 30px rgba(0,0,0,0.45);
    overflow: hidden;
  }
  .card::after {
    content: ""; position: absolute; left: 0; right: 0; bottom: 0;
    height: 9px; background: var(--brand-blue);
  }
  .card--front { top: 76px; }
  .card--back { top: 468px; }

  /* Front */
  .brand {
    position: absolute; top: 92px; left: 0; right: 0;
    display: flex; align-items: center; justify-content: center; gap: 12px;
  }
  .brand__mark {
    width: 16px; height: 16px; background: var(--brand-blue);
  }
  .brand__name {
    font-family: "Lato", sans-serif; font-weight: 700;
    font-size: 27px; color: var(--brand-blue); letter-spacing: 0.2px;
  }
  .services {
    position: absolute; top: 186px; left: 0; right: 0;
    text-align: center;
    font-family: "Arimo", sans-serif; font-size: 16px; line-height: 25px;
    color: var(--text-muted);
  }
  .services .sep { color: var(--brand-blue); padding: 0 6px; }

  /* Back */
  .person {
    position: absolute; top: 120px; left: 92px; width: 210px;
    text-align: right;
  }
  .person__name {
    font-family: "Oswald", sans-serif; font-weight: 500;
    font-size: 30px; line-height: 1; color: var(--brand-blue);
    text-transform: uppercase; letter-spacing: -0.5px;
  }
  .person__role {
    font-family: "Lato", sans-serif; font-size: 16px;
    color: var(--text-light); margin-top: 6px;
  }
  .divider {
    position: absolute; top: 110px; left: 328px;
    width: 1px; height: 96px; background: var(--divider);
  }
  .contacts {
    position: absolute; top: 122px; left: 352px;
    list-style: none;
    font-family: "Lato", sans-serif; font-size: 15.5px; line-height: 25px;
    color: var(--text-light);
  }
  .contacts li { display: flex; align-items: center; gap: 9px; }
  .contacts svg { width: 15px; height: 15px; flex: none; }
  .social {
    position: absolute; bottom: 34px; left: 180px;
    display: flex; align-items: center; gap: 9px;
    font-family: "Lato", sans-serif; font-size: 15.5px; color: var(--text-light);
  }
  .social__mark { width: 16px; height: 16px; background: var(--brand-blue); border-radius: 3px; }
</style>
</head>
<body>
<main class="stage">
  <section class="card card--front" aria-label="Business card front">
    <div class="brand">
      <span class="brand__mark" aria-hidden="true"></span>
      <span class="brand__name">Stonebridge Building and Projects</span>
    </div>
    <p class="services">
      Home improvement projects<span class="sep">|</span>House renovations<br>
      Bathroom and kitchen renovations<br>
      House extensions<span class="sep">|</span>New builds and granny flats
    </p>
  </section>

  <section class="card card--back" aria-label="Business card back">
    <div class="person">
      <p class="person__name">Omar Haddani</p>
      <p class="person__role">Director</p>
    </div>
    <span class="divider" aria-hidden="true"></span>
    <ul class="contacts">
      <li>
        <svg viewBox="0 0 16 16" aria-hidden="true"><path fill="var(--brand-blue)" d="M3.6 1.2l2.2 2.6-1.3 1.6c.9 1.9 2.3 3.3 4.2 4.2l1.6-1.3 2.6 2.2-1 2.3C6.5 12.6 3.4 9.5 1.2 3.6z"/></svg>
        040-555 012 345
      </li>
      <li>
        <svg viewBox="0 0 16 16" aria-hidden="true"><rect x="1" y="3.5" width="14" height="9" fill="var(--brand-blue)"/><path d="M1 3.5l7 5 7-5" fill="none" stroke="var(--card)" stroke-width="1.2"/></svg>
        omar@sbpbuilding.com.au
      </li>
      <li>
        <svg viewBox="0 0 16 16" aria-hidden="true"><g fill="none" stroke="var(--brand-blue)" stroke-width="1.3"><circle cx="8" cy="8" r="6.5"/><ellipse cx="8" cy="8" rx="2.8" ry="6.5"/><path d="M1.5 8h13M2.5 4.8h11M2.5 11.2h11"/></g></svg>
        www.sbpbuilding.com.au
      </li>
    </ul>
    <div class="social">
      <span class="social__mark" aria-hidden="true"></span>
      <span>sbp_building</span>
    </div>
  </section>
</main>
</body>
</html>
```